Kestrel Facilities Business Card Design

We would now like to design business cards with the new Kestrel Facilities logo

Target Market(s)

Professional

Industry/Entity Type

Professional services

Contact Information for Business Card

Employee name, title, phone number, email address, corporate office address and logo.

Font styles to use
Sans Serif

Colors
0054AA
0677BA
7BADD7
CADEEF
E8F1F8

Requirements
Must have
• My logo
Should not have
• any other pictures or images besides my logo

```html
<!DOCTYPE html>
<html lang="en">
<head>
<meta charset="utf-8">
<title>Kestrel Facilities Business Card</title>
<link rel="stylesheet" href="https://fonts.googleapis.com/css2?family=Oswald:wght@500&family=Arimo:wght@400&display=swap">
<style>
  :root {
    --backdrop: #c9c9c9;
    --card-dark: #2a2a2a;
    --brand-blue: #0677ba;
    --bright-blue: #0a84e6;
    --card-blue: #0a80e8;
    --deep-blue: #0054aa;
    --text-light: #e6e6e6;
    --divider: #3a3a3a;
  }
  * { margin: 0; padding: 0; box-sizing: border-box; }
  html, body { width: 1200px; height: 800px; overflow: hidden; }
  body {
    background: var(--backdrop);
    font-family: "Arimo", Arial, sans-serif;
    position: relative;
  }
  .card {
    position: absolute;
    left: 337px;
    width: 525px;
    height: 300px;
    box-shadow: 0 10px 24px rgba(0,0,0,0.25);
  }
  .card-front {
    top: 70px;
    background: var(--card-dark);
    border-bottom: 3px solid var(--bright-blue);
    display: flex;
  }
  .card-back {
    top: 420px;
    background: var(--card-blue);
    display: flex;
    align-items: center;
    justify-content: center;
  }
  .brand-block {
    width: 48%;
    display: flex;
    align-items: center;
    justify-content: center;
    gap: 12px;
    border-right: 1px solid var(--divider);
  }
  .brand-mark {
    width: 34px; height: 34px;
    background: var(--bright-blue);
  }
  .brand-name {
    font-family: "Oswald", "Arial Narrow", sans-serif;
    font-weight: 500;
    font-size: 30px;
    line-height: 1.05;
    letter-spacing: 1px;
    text-transform: uppercase;
    color: var(--bright-blue);
  }
  .contact-block {
    flex: 1;
    padding: 48px 0 0 32px;
    color: var(--text-light);
  }
  .person-name {
    font-family: "Oswald", "Arial Narrow", sans-serif;
    font-weight: 500;
    font-size: 26px;
    color: var(--bright-blue);
    text-transform: uppercase;
    line-height: 1.1;
  }
  .person-title { font-size: 14px; margin-bottom: 18px; }
  .contact-list { list-style: none; font-size: 14px; line-height: 1.6; }
  .contact-list li { display: flex; align-items: center; gap: 8px; }
  .contact-list svg { width: 13px; height: 13px; flex: none; }
  .web-accent { color: var(--bright-blue); }
  .address { margin-top: 16px; font-size: 14px; line-height: 1.4; }
  .back-name {
    font-family: "Oswald", "Arial Narrow", sans-serif;
    font-weight: 500;
    font-size: 52px;
    letter-spacing: 2px;
    text-transform: uppercase;
    color: var(--deep-blue);
  }
</style>
</head>
<body>
  <section class="card card-front">
    <div class="brand-block">
      <span class="brand-mark"></span>
      <span class="brand-name">Kestrel<br>Facilities</span>
    </div>
    <div class="contact-block">
      <h1 class="person-name">Daniel Hart</h1>
      <p class="person-title">Managing Director</p>
      <ul class="contact-list">
        <li>
          <svg viewBox="0 0 16 16"><path fill="#0a84e6" d="M3 1l3 3-2 2c1 2 3 4 5 5l2-2 3 3-2 3C7 15 1 9 1 3z"/></svg>
          044-555 010 234
        </li>
        <li>
          <svg viewBox="0 0 16 16"><rect x="1" y="3" width="14" height="10" fill="#0a84e6"/><path d="M1 3l7 6 7-6" fill="none" stroke="#2a2a2a" stroke-width="1.5"/></svg>
          info@kestrelfm.com
        </li>
        <li>
          <svg viewBox="0 0 16 16"><circle cx="8" cy="8" r="7" fill="#0a84e6"/><path d="M1 8h14M8 1c-3 4-3 10 0 14M8 1c3 4 3 10 0 14" fill="none" stroke="#2a2a2a" stroke-width="1"/></svg>
          <span>www.<span class="web-accent">kestrelfm</span>.com</span>
        </li>
      </ul>
      <p class="address">18, Harbour Row Business Park<br>73018, Northland</p>
    </div>
  </section>

  <section class="card card-back">
    <span class="back-name">Kestrel Facilities</span>
  </section>
</body>
</html>
```